Whitcombe Business Card Design

The name of the business is Dario Whitcombe, CPA LLC
The service that we offer is Accounting, Tax & Consulting Services. I need it to have the following items:
Dario Whitcombe, Principal
Phone Number
Email Address
Physical Address

I have attached the company logo, one in black and one in white. Please provide a design in black background and the other in white background. Please include "Accounting, Tax & Consulting Services". I want the business card to be clean and very professional.

```html
<!DOCTYPE html>
<html lang="en">
<head>
<meta charset="utf-8">
<title>Dario Whitcombe, CPA LLC – Business Card</title>
<link href="https://fonts.googleapis.com/css2?family=Lato:wght@400;700&family=Oswald:wght@500&display=swap" rel="stylesheet">
<style>
  :root {
    --backdrop: #262626;
    --card: #111112;
    --accent: #9e1a1f;
    --text-grey: #8a8a8a;
    --text-light: #a9a9a9;
    --mark-grey: #5a5a5a;
  }
  * { margin: 0; padding: 0; box-sizing: border-box; }
  html, body { width: 1200px; height: 900px; overflow: hidden; }
  body {
    background: var(--backdrop);
    font-family: "Lato", Arial, sans-serif;
    position: relative;
  }
  .card {
    position: absolute;
    left: 250px;
    width: 700px;
    height: 400px;
    background: var(--card);
    box-shadow: 0 8px 24px rgba(0,0,0,.5);
    overflow: hidden;
  }
  .card::after {
    content: "";
    position: absolute;
    left: 0; right: 0; bottom: 0;
    height: 10px;
    background: var(--accent);
  }
  .card--front { top: 35px; }
  .card--back { top: 465px; }

  /* Front */
  .brand {
    position: absolute;
    top: 120px;
    left: 0; right: 0;
    display: flex;
    flex-direction: column;
    align-items: center;
  }
  .brand__lockup {
    display: flex;
    align-items: center;
    gap: 14px;
  }
  .brand__square {
    width: 22px; height: 22px;
    background: var(--accent);
  }
  .brand__name {
    font-weight: 700;
    font-size: 30px;
    letter-spacing: 2px;
    color: var(--mark-grey);
    text-transform: uppercase;
  }
  .brand__title {
    margin-top: 6px;
    font-weight: 700;
    font-size: 19px;
    letter-spacing: 4.5px;
    color: var(--text-grey);
    text-transform: uppercase;
  }
  .services {
    position: absolute;
    bottom: 62px;
    left: 0; right: 0;
    text-align: center;
    font-size: 19px;
    letter-spacing: 1px;
    color: var(--text-light);
    text-transform: uppercase;
  }

  /* Back */
  .person {
    position: absolute;
    top: 130px;
    right: 390px;
    text-align: right;
  }
  .person__name {
    font-family: "Oswald", "Arial Narrow", sans-serif;
    font-weight: 500;
    font-size: 40px;
    line-height: 1;
    color: var(--accent);
    text-transform: uppercase;
    letter-spacing: -0.5px;
  }
  .person__role {
    margin-top: 4px;
    font-size: 20px;
    color: var(--text-grey);
  }
  .divider {
    position: absolute;
    top: 130px;
    left: 340px;
    width: 1px;
    height: 70px;
    background: var(--text-grey);
  }
  .contact {
    position: absolute;
    top: 140px;
    left: 362px;
    list-style: none;
  }
  .contact__item {
    display: flex;
    align-items: center;
    gap: 10px;
    font-size: 20px;
    color: var(--text-light);
    line-height: 28px;
  }
  .contact__icon { width: 18px; height: 18px; flex: none; }
  .address {
    position: absolute;
    bottom: 52px;
    left: 0; right: 0;
    text-align: center;
    font-size: 20px;
    color: var(--text-light);
  }
</style>
</head>
<body>
  <section class="card card--front">
    <div class="brand">
      <div class="brand__lockup">
        <span class="brand__square"></span>
        <span class="brand__name">Dario Whitcombe, CPA LLC</span>
      </div>
      <div class="brand__title">Certified Public Accountant</div>
    </div>
    <p class="services">Accounting, Tax &amp; Consulting Services</p>
  </section>

  <section class="card card--back">
    <div class="person">
      <div class="person__name">Dario Whitcombe</div>
      <div class="person__role">Principal</div>
    </div>
    <span class="divider"></span>
    <ul class="contact">
      <li class="contact__item">
        <svg class="contact__icon" viewBox="0 0 24 24" aria-hidden="true"><path fill="#9e1a1f" d="M6.6 10.8c1.4 2.8 3.8 5.1 6.6 6.6l2.2-2.2c.3-.3.7-.4 1-.2 1.1.4 2.3.6 3.6.6.6 0 1 .4 1 1V20c0 .6-.4 1-1 1C10.6 21 3 13.4 3 4c0-.6.4-1 1-1h3.5c.6 0 1 .4 1 1 0 1.3.2 2.5.6 3.6.1.3 0 .7-.2 1z"/></svg>
        044-123 456 789
      </li>
      <li class="contact__item">
        <svg class="contact__icon" viewBox="0 0 24 24" aria-hidden="true"><rect x="2" y="5" width="20" height="14" fill="#9e1a1f"/><path d="M2 5l10 8 10-8" fill="none" stroke="#111112" stroke-width="1.6"/></svg>
        info@webname.com
      </li>
    </ul>
    <p class="address">421, Address line here, Country Name, 45452</p>
  </section>
</body>
</html>
```